New, modern business card for growing audiology practice

We need a new business card for our audiology practice. Our logo and website have recently changed (more modern) and we want our business cards to reflect this change.
We conduct hearing tests, perform earwax removals, and fit & dispense hearing aids to our patients. We are a family owned practice in which the owner is the one who works directly with the patient. I have attached logos in various formats to use, as well as two ideas I found on this website; as well as a scanned copy of our current logo. Good luck!

Industry/Entity Type

Business

Contact Information for Business Card

Company name: Tolvera Hearing Center
Provider name: Peter Wolstenby, Au.D. F/NSB
Phone number: (440) 683-5127
Address: 837 W. Lindell Ave. Marlow Creek, OH 44371
email: tolverahearing@postvane.com
website: tolverahearing.com

Colors
000000
aaaaaa
dbdbdb
cacaca
9bcb3c
afd23c
cadf82
b1b1b1

Requirements
Must have
• My card must include information in the "details" section. In the attached images, I found a few that I liked and I would like to model after - "brisky bouncin'" and "Sound Method Center".
• Must be horizontal.
• Must include logos provided. I uploaded them in various file formats and various ways.
• Must match logo font, if possible, if not, please get as close as you can.
Nice to have
• I really like the idea of having a color on one side with just the logo and company name and the contact information and provider name on the other side. I also really like the idea of having the main color dominating on the logo/company side with accent of that same color on the contact side of the card.
Should not have
• Must not be vertical.

```html
<!DOCTYPE html>
<html lang="en">
<head>
<meta charset="utf-8">
<title>Tolvera Hearing Center – Business Card</title>
<link rel="stylesheet" href="https://fonts.googleapis.com/css2?family=Roboto:wght@400;500;700&family=Roboto+Condensed:wght@700&display=swap">
<style>
  :root {
    --backdrop: #e4e2de;
    --card-light: #f3f3f3;
    --card-dark: #1c1d1f;
    --brand-green: #79a63a;
    --ink: #111111;
    --text-grey: #4a4a4a;
    --white: #ffffff;
  }
  * { margin: 0; padding: 0; box-sizing: border-box; }
  html, body {
    width: 1200px; height: 960px; overflow: hidden;
    background: var(--backdrop);
    font-family: "Roboto", Arial, sans-serif;
  }
  .canvas { position: relative; width: 1200px; height: 960px; }

  .card {
    position: absolute; width: 600px; height: 344px;
    border-radius: 20px; overflow: hidden;
    box-shadow: 0 2px 6px rgba(0,0,0,.25);
  }
  .card--front { left: 314px; top: 113px; background: var(--card-light); }
  .card--back  { left: 311px; top: 471px; background: var(--card-dark); }

  .brand {
    position: absolute; left: 46px; top: 58px;
    display: flex; align-items: center; gap: 9px;
  }
  .brand__dot { width: 12px; height: 12px; border-radius: 50%; background: var(--brand-green); }
  .brand__name {
    font-size: 18px; font-weight: 400; letter-spacing: .1px;
    color: var(--ink); text-transform: uppercase;
  }

  .contact {
    position: absolute; left: 45px; top: 166px;
    font-size: 14px; line-height: 19px; color: var(--text-grey);
  }
  .contact__address { margin-bottom: 9px; }
  .contact__line { display: flex; align-items: center; gap: 8px; }
  .contact__icon { width: 13px; height: 13px; flex: none; }

  .provider {
    position: absolute; right: 47px; top: 186px; text-align: right;
  }
  .provider__name {
    font-family: "Roboto Condensed", "Arial Narrow", sans-serif;
    font-weight: 700; font-size: 21px; color: var(--brand-green);
    text-transform: uppercase; line-height: 26px;
  }
  .provider__credentials {
    font-size: 15px; font-weight: 700; color: var(--ink);
    text-transform: uppercase; line-height: 22px;
  }

  .wave { position: absolute; left: 0; top: 0; width: 600px; height: 344px; }
  .card__website--front {
    position: absolute; right: 53px; top: 310px;
    font-size: 15px; letter-spacing: 1.3px; color: var(--white);
  }

  .back-brand {
    position: absolute; left: 0; right: 0; top: 120px;
    display: flex; flex-direction: column; align-items: center; gap: 18px;
  }
  .back-brand__dot { width: 58px; height: 58px; border-radius: 50%; background: var(--brand-green); }
  .back-brand__name {
    font-size: 26px; font-weight: 500; color: var(--brand-green);
    text-transform: uppercase; letter-spacing: 1px;
  }
  .card__website--back {
    position: absolute; left: 0; right: 0; top: 294px; text-align: center;
    font-size: 15px; letter-spacing: 3.6px; color: var(--white);
  }
</style>
</head>
<body>
<main class="canvas">

  <section class="card card--front" aria-label="Card front">
    <div class="brand">
      <span class="brand__dot"></span>
      <span class="brand__name">Tolvera Hearing Center</span>
    </div>

    <div class="contact">
      <p class="contact__address">837 W. Lindell Ave.<br>Marlow Creek, OH 44371</p>
      <p class="contact__line">
        <svg class="contact__icon" viewBox="0 0 24 24" aria-hidden="true"><path fill="#79a63a" d="M6.6 10.8a15.2 15.2 0 0 0 6.6 6.6l2.2-2.2c.3-.3.7-.4 1-.2 1.1.4 2.3.6 3.6.6.6 0 1 .4 1 1V20c0 .6-.4 1-1 1A17 17 0 0 1 3 4c0-.6.4-1 1-1h3.5c.6 0 1 .4 1 1 0 1.3.2 2.5.6 3.6.1.3 0 .7-.2 1z"/></svg>
        (440) 683-5127
      </p>
      <p class="contact__line">
        <svg class="contact__icon" viewBox="0 0 24 24" aria-hidden="true"><path fill="#79a63a" d="M2 5h20v14H2z"/><path fill="none" stroke="#f3f3f3" stroke-width="1.8" d="M2.5 5.5 12 13l9.5-7.5"/></svg>
        tolverahearing@postvane.com
      </p>
    </div>

    <div class="provider">
      <p class="provider__name">Peter Wolstenby</p>
      <p class="provider__credentials">Au.D. F/NSB</p>
    </div>

    <svg class="wave" viewBox="0 0 600 344" aria-hidden="true">
      <path fill="#79a63a" d="M0 272 C40 305 90 322 160 322 C300 322 420 284 520 284 C560 284 590 302 600 314 L600 344 L0 344 Z"/>
      <path fill="#111111" d="M0 276 C50 310 110 322 180 320 C320 313 430 266 520 267 C565 268 590 290 600 305 L600 316 C585 300 560 282 520 282 C420 282 300 322 160 324 C90 324 40 305 0 282 Z"/>
      <path fill="none" stroke="#ffffff" stroke-width="3" d="M130 326 C290 320 420 288 520 288 C560 289 588 306 600 320"/>
    </svg>
    <p class="card__website--front">www.tolverahearing.com</p>
  </section>

  <section class="card card--back" aria-label="Card back">
    <div class="back-brand">
      <span class="back-brand__dot"></span>
      <span class="back-brand__name">Tolvera Hearing Center</span>
    </div>
    <p class="card__website--back">www.tolverahearing.com</p>
  </section>

</main>
</body>
</html>
```